Presentation Of Our Epidemiology Consulting Framework

We need a slide deck (png files) for PowerPoint that describes our organization and type of clients we serve, and our 6 phase framework that explains how we work with clients. Please use the minimum amount of text on each slide.  We want a more visual display of how to work with us. We want it to look very similar to our brochure.  We want to also have a few extra branded slides without text that can be used as a template if we decide to add to the deck later or create a new slide deck.
Colors
#56588C
#F28444
#F2E088
#F24C27
#ODODOD

```html
<!DOCTYPE html>
<html lang="en">
<head>
<meta charset="utf-8">
<title>Dr Kestrel — Framework Deck Overview</title>
<link href="https://fonts.googleapis.com/css2?family=Poppins:wght@400;500;600;700;800&display=swap" rel="stylesheet">
<style>
:root{
  --indigo:#56588C;
  --navy-top:#3f3d75;
  --navy-bottom:#1e1d3e;
  --orange:#F28444;
  --flame:#F24C27;
  --sand:#F2E088;
  --ink:#0D0D0D;
  --white:#ffffff;
  --paper:#ffffff;
}
*{box-sizing:border-box;margin:0;padding:0}
html,body{width:1200px;height:807px;overflow:hidden;background:var(--paper)}
body{font-family:"Poppins",sans-serif;color:var(--white);position:relative}
.slide{position:absolute;width:350px;height:197px;overflow:hidden;
  background:linear-gradient(180deg,var(--navy-top),var(--navy-bottom));
  box-shadow:0 4px 12px rgba(0,0,0,.28)}
.slide--light{background:var(--white);color:var(--ink)}
.col-1{left:33px}.col-2{left:425px}.col-3{left:817px}
.row-1{top:52px}.row-2{top:307px}.row-3{top:562px}
.abs{position:absolute}
.brand{position:absolute;top:9px;right:8px;font-weight:600;font-size:10px;color:var(--orange);display:flex;align-items:center;gap:3px;white-space:nowrap}
.brand::before{content:"";width:6px;height:6px;border-radius:50%;background:var(--orange)}
.accent-bar{position:absolute;left:0;width:3px;background:var(--white)}
.slide--light .accent-bar{background:var(--indigo)}
.heading{position:absolute;left:6px;font-size:9.5px;font-weight:500;white-space:nowrap}
.heading b{color:var(--orange);font-weight:700}
.sub{position:absolute;left:6px;font-size:6px;white-space:nowrap}
.footer{position:absolute;left:0;right:0;top:184px;height:11px}
.footer .mail{position:absolute;left:6px;top:1px;font-size:4.4px;display:flex;align-items:center;gap:3px;color:var(--white)}
.slide--light .footer .mail{color:var(--ink)}
.footer .mail i{width:8px;height:8px;border-radius:50%;background:var(--orange);display:block}
.footer .bar{position:absolute;left:80px;right:25px;top:0;height:11px;background:var(--white)}
.slide--light .footer .bar{background:var(--indigo)}
.footer .page{position:absolute;right:0;top:0;width:25px;height:11px;background:var(--orange);font-size:4px;line-height:11px;text-align:center;color:var(--white)}
.photo{position:absolute;border-radius:1px}
.photo--warm{background:linear-gradient(135deg,#9a7a68,#5a5a7a 55%,#b98a62)}
.photo--cool{background:linear-gradient(135deg,#c9c4c0,#7a7f96 50%,#e0a070)}
/* title slide */
.cover-brand{position:absolute;top:14px;left:0;right:0;text-align:center;font-size:28px;font-weight:600;color:var(--orange);display:flex;justify-content:center;align-items:center;gap:6px}
.cover-brand::before{content:"";width:18px;height:18px;border-radius:50%;background:var(--orange)}
.cover-title{position:absolute;top:60px;left:0;right:0;text-align:center;font-weight:800;font-size:15px;line-height:20px}
.cover-title span{display:block;color:var(--orange)}
/* agenda */
.agenda-item{position:absolute;width:126px;height:16px;background:var(--ink);color:var(--white);font-size:4.4px;line-height:16px;padding-left:8px;white-space:nowrap}
.agenda-item .num{position:absolute;right:0;top:0;width:20px;height:16px;text-align:center;background:var(--orange);font-weight:600;font-size:4.6px;letter-spacing:0}
.agenda-item.alt .num{background:var(--indigo)}
.agenda-item--long{font-size:3.5px;letter-spacing:-.12px;padding-left:8px}
.body-copy{position:absolute;font-size:5.3px;line-height:8.2px}
/* timeline */
.node{position:absolute;width:8px;height:8px;border-radius:50%;border:1px solid var(--orange);background:transparent}
.node::after{content:"";position:absolute;left:1.5px;top:1.5px;width:3px;height:3px;border-radius:50%;background:var(--orange)}
.tl-label{position:absolute;font-size:5.3px;line-height:8px;text-align:center;font-weight:500}
/* cards */
.caption{position:absolute;top:141px;width:71px;height:22px;background:var(--white);color:var(--ink);border-radius:2px;font-size:4.2px;line-height:5.5px;text-align:center;display:flex;align-items:center;justify-content:center;padding:0 6px}
.launch-card{position:absolute;width:63px;height:29px;background:var(--white);color:var(--ink);border-radius:2px;font-size:3.9px;line-height:4.8px;text-align:center;padding:13px 4px 0}
.launch-card .icon{position:absolute;top:-9px;left:23px;width:17px;height:17px;border-radius:50%;background:var(--orange);border:2px solid var(--white)}
.bullets{position:absolute;left:14px;top:84px;width:152px;list-style:none;font-size:4.5px;line-height:10.3px;letter-spacing:-.05px;white-space:nowrap}
.bullets li{position:relative;padding-left:7px}
.bullets li::before{content:"";position:absolute;left:0;top:4px;width:3px;height:3px;border-radius:50%;background:var(--orange)}
.cta-title{position:absolute;left:11px;top:58px;font-weight:800;font-size:14px;line-height:18px}
.cta-title span{color:var(--orange)}
.cta-copy{position:absolute;left:11px;top:98px;font-size:6px;line-height:10px;font-style:italic}
.cta-mail{position:absolute;left:6px;top:170px;height:14px;padding:0 8px 0 5px;border-radius:7px;background:rgba(20,20,40,.7);display:flex;align-items:center;gap:4px;font-size:5px;text-decoration:underline}
.cta-mail i{width:8px;height:8px;border-radius:50%;background:var(--orange);display:block}
</style>
</head>
<body>

<!-- 1 cover -->
<section class="slide col-1 row-1">
  <div class="cover-brand">Dr Kestrel</div>
  <h1 class="cover-title"><span>Transforming Health Data into</span>Community Impact</h1>
  <div class="photo abs" role="img" aria-label="Crowd of small figures on pillars reaching upward toward one leader" style="left:0;right:0;top:105px;bottom:0;background:linear-gradient(180deg,rgba(60,58,110,0),#2a2950 40%,#3a3566)"></div>
</section>

<!-- 2 agenda -->
<section class="slide slide--light col-2 row-1">
  <div class="accent-bar" style="top:10px;height:12px"></div>
  <div class="heading" style="top:9px;font-weight:700">Agenda</div>
  <div class="brand">Dr Kestrel</div>
  <div class="agenda-item" style="left:38px;top:47px">01. Agenda<span class="num">01</span></div>
  <div class="agenda-item alt" style="left:177px;top:47px">02. Our Approach<span class="num">02</span></div>
  <div class="agenda-item" style="left:38px;top:70px">03. Discovery &amp; Vision Alignment<span class="num">03</span></div>
  <div class="agenda-item alt" style="left:177px;top:70px">04. Partnership Launch<span class="num">04</span></div>
  <div class="agenda-item" style="left:38px;top:93px">05. Expert Execution<span class="num">05</span></div>
  <div class="agenda-item alt" style="left:177px;top:93px">06. Collaborative Refinement<span class="num">06</span></div>
  <div class="agenda-item" style="left:38px;top:116px">07. Impact Delivery<span class="num">07</span></div>
  <div class="agenda-item alt" style="left:177px;top:116px">08. Evolution &amp; Growth<span class="num">08</span></div>
  <div class="agenda-item" style="left:38px;top:139px">09. Why Partner With Us?<span class="num">09</span></div>
  <div class="agenda-item alt agenda-item--long" style="left:177px;top:139px">10. Ready to Transform Your Health Communication?<span class="num">10</span></div>
  <footer class="footer"><span class="mail"><i></i>support@drkestrel.com</span><span class="bar"></span><span class="page">Page 02</span></footer>
</section>

<!-- 3 about -->
<section class="slide col-3 row-1">
  <div class="accent-bar" style="top:11px;height:11px"></div>
  <div class="heading" style="top:10px">Transforming Health Data into Community Impact:</div>
  <div class="heading" style="top:24px"><b>The Dr Kestrel Framework</b></div>
  <div class="brand">Dr Kestrel</div>
  <div class="photo photo--warm" role="img" aria-label="Community members gathered with a wheelchair user" style="left:39px;top:61px;width:51px;height:49px"></div>
  <div class="photo photo--cool" role="img" aria-label="Group discussion in a circle of chairs" style="left:93px;top:61px;width:51px;height:49px"></div>
  <div class="photo photo--cool" role="img" aria-label="Elders talking at a community meeting" style="left:39px;top:113px;width:51px;height:49px"></div>
  <div class="photo photo--warm" role="img" aria-label="Women sharing a conversation over coffee" style="left:93px;top:113px;width:51px;height:49px"></div>
  <p class="body-copy" style="left:161px;top:80px;width:155px;text-align:justify">Dr Kestrel LLC is an epidemiology consulting firm that supports large nonprofit organizations and government agencies that serve black, indigenous, and people of color commonly referred to as BIPOC communities. Our diverse team of innovative global public health professionals are ready to serve your organization by helping you address your most pressing challenges.</p>
  <footer class="footer"><span class="mail"><i></i>support@drkestrel.com</span><span class="bar"></span><span class="page">Page 03</span></footer>
</section>

<!-- 4 approach -->
<section class="slide col-1 row-2">
  <div class="brand">Dr Kestrel</div>
  <div class="accent-bar" style="top:54px;height:12px"></div>
  <div class="heading" style="top:53px">Our <b>Approach</b></div>
  <p class="body-copy" style="left:9px;top:80px;width:190px">At Dr Kestrel LLC, we believe in transforming health data into actionable insights for BIPOC communities. Our proven six-phase partnership model ensures your organization's success in communicating vital health information effectively.</p>
  <div class="photo" role="img" aria-label="Portrait of the firm's founder in a dark blazer" style="left:245px;top:32px;width:105px;height:152px;background:linear-gradient(180deg,rgba(60,58,110,0),#2b2a2e 45%,#1c1c22)"></div>
  <footer class="footer"><span class="mail"><i></i>support@drkestrel.com</span><span class="bar"></span><span class="page">Page 04</span></footer>
</section>

<!-- 5 discovery -->
<section class="slide col-2 row-2">
  <div class="brand">Dr Kestrel</div>
  <div class="accent-bar" style="top:24px;height:11px"></div>
  <div class="heading" style="top:22px">Discovery &amp; <b>Vision Alignment</b></div>
  <div class="sub" style="top:36px">Building the Foundation for Success</div>
  <svg class="abs" style="left:0;top:0" width="350" height="197" aria-hidden="true">
    <line x1="76" y1="99" x2="299" y2="99" stroke="#ffffff" stroke-width=".6" stroke-dasharray="1.5 1.5"/>
    <g stroke="#ffffff" stroke-width=".6" fill="none">
      <line x1="76" y1="104" x2="76" y2="114"/><path d="M74.5 112 L76 114 L77.5 112"/>
      <line x1="213" y1="104" x2="213" y2="114"/><path d="M211.5 112 L213 114 L214.5 112"/>
      <line x1="146" y1="84" x2="146" y2="94"/><path d="M144.5 86 L146 84 L147.5 86"/>
      <line x1="298" y1="84" x2="298" y2="94"/><path d="M296.5 86 L298 84 L299.5 86"/>
    </g>
  </svg>
  <span class="node" style="left:72px;top:95px"></span>
  <span class="node" style="left:142px;top:95px"></span>
  <span class="node" style="left:209px;top:95px"></span>
  <span class="node" style="left:294px;top:95px"></span>
  <div class="tl-label" style="left:106px;top:63px;width:80px">Strategic alignment of goals and expectations</div>
  <div class="tl-label" style="left:248px;top:63px;width:100px">Clear roadmap development with defined milestones</div>
  <div class="tl-label" style="left:30px;top:117px;width:92px">Deep-dive exploration of your organization's unique challenges and opportunities</div>
  <div class="tl-label" style="left:178px;top:117px;width:70px">Custom-tailored solution design</div>
  <footer class="footer"><span class="mail"><i></i>support@drkestrel.com</span><span class="bar"></span><span class="page">Page 05</span></footer>
</section>

<!-- 6 refinement -->
<section class="slide col-3 row-2">
  <div class="brand">Dr Kestrel</div>
  <div class="accent-bar" style="top:24px;height:11px"></div>
  <div class="heading" style="top:22px">Collaborative <b>Refinement</b></div>
  <div class="sub" style="top:36px">Ensuring Perfect Alignment</div>
  <div class="photo photo--cool" role="img" aria-label="Consultant presenting a framework to a client" style="left:25px;top:54px;width:71px;height:83px"></div>
  <div class="photo photo--warm" role="img" aria-label="Team member sharing notes in a feedback session" style="left:101px;top:54px;width:71px;height:83px"></div>
  <div class="photo photo--cool" role="img" aria-label="Group of colleagues reviewing a draft together" style="left:178px;top:54px;width:71px;height:83px"></div>
  <div class="photo photo--warm" role="img" aria-label="Many hands joined in a circle" style="left:254px;top:54px;width:71px;height:83px"></div>
  <div class="caption" style="left:25px">Presentation of initial frameworks</div>
  <div class="caption" style="left:101px">Interactive feedback sessions</div>
  <div class="caption" style="left:178px">Draft review and optimization</div>
  <div class="caption" style="left:254px">Stakeholder input integration</div>
  <footer class="footer"><span class="mail"><i></i>support@drkestrel.com</span><span class="bar"></span><span class="page">Page 06</span></footer>
</section>

<!-- 7 launch -->
<section class="slide col-1 row-3">
  <div class="brand">Dr Kestrel</div>
  <div class="accent-bar" style="top:24px;height:11px"></div>
  <div class="heading" style="top:22px">Partnership <b>Launch</b></div>
  <div class="sub" style="top:36px">Setting the Stage for Excellence</div>
  <div class="launch-card" style="left:7px;top:100px"><span class="icon"></span>Formation of dedicated project team</div>
  <div class="launch-card" style="left:75px;top:85px"><span class="icon"></span>Establishment of collaborative workflow</div>
  <div class="launch-card" style="left:142px;top:100px"><span class="icon"></span>Comprehensive data gathering</div>
  <div class="launch-card" style="left:210px;top:85px"><span class="icon"></span>Strategic timeline planning</div>
  <div class="launch-card" style="left:277px;top:100px"><span class="icon"></span>Stakeholder engagement and vision capture</div>
  <footer class="footer"><span class="mail"><i></i>support@drkestrel.com</span><span class="bar"></span><span class="page">Page 08</span></footer>
</section>

<!-- 8 execution -->
<section class="slide col-2 row-3">
  <div class="brand">Dr Kestrel</div>
  <div class="accent-bar" style="top:24px;height:11px"></div>
  <div class="heading" style="top:22px">Expert <b>Execution</b></div>
  <div class="sub" style="top:36px">Where Science Meets Service</div>
  <div class="sub" style="top:47px;font-size:4.6px">Our specialized team begins the transformation process:</div>
  <ul class="bullets">
    <li>In-depth research and analysis</li>
    <li>Content development and refinement</li>
    <li>Data interpretation and visualization</li>
    <li>Plain language translation of complex health information</li>
  </ul>
  <div class="photo photo--warm" role="img" aria-label="Joyful diverse crowd waving at the camera" style="left:172px;top:48px;width:161px;height:104px;border-radius:3px"></div>
  <footer class="footer"><span class="mail"><i></i>support@drkestrel.com</span><span class="bar"></span><span class="page">Page 08</span></footer>
</section>

<!-- 9 call to action -->
<section class="slide col-3 row-3">
  <div class="photo" role="img" aria-label="Colleagues laughing around a meeting table" style="left:0;top:0;width:350px;height:197px;background:linear-gradient(100deg,rgba(40,38,80,.95),rgba(70,60,90,.75) 55%,#6a5a5a)"></div>
  <div class="abs" style="right:12px;top:20px;font-size:6px">www.drkestrel.com</div>
  <h2 class="cta-title"><span>Ready to Transform Your</span><br>Health Communication?</h2>
  <p class="cta-copy">Contact us to begin your journey toward more effective,<br>equitable health communication.</p>
  <div class="cta-mail"><i></i>support@drkestrel.com</div>
  <div class="abs" style="right:8px;top:162px;font-size:20px;font-weight:600;color:var(--orange);display:flex;align-items:center;gap:4px"><span style="width:12px;height:12px;border-radius:50%;background:var(--orange);display:block"></span>Dr Kestrel</div>
</section>

</body>
</html>
```